Laser Tattoo Removal Business Cards

We are looking for a professional business card design for a laser tattoo removal business. Ideally looking for a black business card design. The name of the business is Brightline Tattoo Removal. We place our cards at local tattoo shops so we ideally are looking for something trendy/edgy to draw both male and female clientele in.

Target Market(s)

Male/Female ages 18-60

Contact Information for Business Card

black background ideally.. hoping to stay within greys, whites and black

Font styles to use
Serif
Sans Serif

Colors
121212
a9a9a9
5c5c5c
f5f5f5
ffffff
7f7f7f
606060
848484
9d9d9d

Requirements
Must have
• Employee Info:
• Melissa Thornbury
• Chief Executive Offer
• m: 919.537.2846
• w: 919.362.4178
• f: 919.685.3907
• mthornbury@brightlinetattooremoval.example
• Address:
• 4615 Oakmere Pkwy, Suite 210
• Raleigh, NC 27654
• Website:
• www.brightlinetattooremoval.example
Nice to have
• Myabe business name on back or logo on back and employee info on the front

```html
<!DOCTYPE html>
<html lang="en">
<head>
<meta charset="utf-8">
<title>Brightline Tattoo Removal – Business Cards</title>
<link rel="stylesheet" href="https://fonts.googleapis.com/css2?family=Oswald:wght@400;500&family=Figtree:wght@400;600;700&display=swap">
<style>
  :root {
    --ink: #121212;
    --card-dark: #1c1d1f;
    --paper: #ffffff;
    --grey-dark: #5c5c5c;
    --grey-mid: #7f7f7f;
    --grey-title: #848484;
    --grey-rule: #9d9d9d;
    --grey-light: #a9a9a9;
    --off-white: #f5f5f5;
    --bg-left: #d2d2d2;
    --bg-right: #868686;
  }
  * { margin: 0; padding: 0; box-sizing: border-box; }
  html, body { width: 1200px; height: 960px; overflow: hidden; }
  body {
    position: relative;
    background: linear-gradient(90deg, var(--bg-left) 0%, #b4b4b4 45%, var(--bg-right) 100%);
    font-family: "Figtree", "Helvetica Neue", Arial, sans-serif;
  }

  .card { position: absolute; width: 600px; height: 343px; }
  .card__frame { position: absolute; inset: 9px; }

  /* Front */
  .card--front { left: 302px; top: 122px; background: var(--paper); }
  .card--front .card__frame { border: 1px solid var(--ink); }
  .contact { position: absolute; left: 0; right: 0; top: 0; text-align: center; color: var(--grey-dark); }
  .contact__name {
    position: absolute; left: 0; right: 0; top: 78px;
    font-family: "Oswald", "Arial Narrow", sans-serif; font-weight: 400;
    font-size: 36px; line-height: 44px; letter-spacing: 0.5px; color: #222222;
    transform: scaleX(0.82);
  }
  .contact__title {
    position: absolute; left: 0; right: 0; top: 120px;
    font-size: 13.5px; font-weight: 600; letter-spacing: 0.4px; color: var(--grey-title);
  }
  .rule { position: absolute; left: 274px; width: 51px; height: 2px; background: var(--grey-rule); }
  .rule--top { top: 151px; }
  .rule--bottom { top: 232px; }
  .contact__lines { position: absolute; left: 0; right: 0; top: 165px; font-size: 13.5px; line-height: 18px; }
  .contact__lines b { font-weight: 700; color: #2a2a2a; }
  .contact__web {
    position: absolute; left: 0; right: 0; top: 247px;
    font-size: 13.5px; letter-spacing: 1.6px; color: var(--grey-dark);
  }
  .contact__web strong { font-weight: 700; color: #3a3a3a; }

  /* Back */
  .card--back { left: 299px; top: 495px; background: var(--card-dark); }
  .card--back .card__frame { border: 1px solid var(--grey-mid); }
  .brand { position: absolute; left: 0; right: 0; text-align: center; color: var(--off-white);
    font-family: "Oswald", "Arial Narrow", sans-serif; font-weight: 400; }
  .brand__name { top: 98px; font-size: 50px; line-height: 60px; letter-spacing: 4px; }
  .brand__sub { top: 225px; font-size: 20px; line-height: 26px; letter-spacing: 4px; }
</style>
</head>
<body>
  <section class="card card--front" aria-label="Business card front">
    <div class="card__frame"></div>
    <div class="contact">
      <h1 class="contact__name">MELISSA THORNBURY</h1>
      <p class="contact__title">CHIEF EXECUTIVE OFFER</p>
      <div class="rule rule--top"></div>
      <p class="contact__lines">
        4615 Oakmere Pkwy, Suite 210, Raleigh, NC 27654<br>
        <b>M</b>: 919.537.2846 <b>W</b>: 919.362.4178 <b>F</b>: 919.685.3907<br>
        mthornbury@brightlinetattooremoval.example
      </p>
      <div class="rule rule--bottom"></div>
      <p class="contact__web">www.<strong>brightlinetattooremoval</strong>.example</p>
    </div>
  </section>

  <section class="card card--back" aria-label="Business card back">
    <div class="card__frame"></div>
    <p class="brand brand__name">BRIGHTLINE</p>
    <p class="brand brand__sub">TATTOO REMOVAL</p>
  </section>
</body>
</html>
```